Design a website for our small self storage business

We're looking for a freelance web designer who can produce a good-looking design for our small business website (no coding necessary). We will provide a list of pages to design, along with content outlines.

Key skills:
- Graphic design
- Responsive web design
- Proficiency with a modern web design tool such as Figma, Adobe Xd, or InVision

Please send relevant previous work (preferably in an inspectable format such as Figma or Invision).

```html
<!DOCTYPE html>
<html lang="en">
<head>
<meta charset="utf-8">
<title>Baycrest Self Storage</title>
<link href="https://fonts.googleapis.com/css2?family=Oswald:wght@400;500;600&family=Roboto:wght@400;500;700&display=swap" rel="stylesheet">
<style>
:root{
  --red:#d7161f;
  --red-dark:#b80e17;
  --navy:#0f3a80;
  --navy-dark:#0b2c63;
  --ink:#1c1c1c;
  --text:#4b4b4b;
  --muted:#8a8a8a;
  --line:#d9d9d9;
  --paper:#ffffff;
  --mist:#f3f4f6;
}
*{box-sizing:border-box;margin:0;padding:0}
html,body{width:1200px;height:4766px;overflow:hidden}
body{font-family:"Roboto",sans-serif;color:var(--text);background:var(--paper);position:relative}
.heading{font-family:"Oswald",sans-serif;font-weight:500;color:var(--navy)}
.abs{position:absolute}
.btn{display:flex;align-items:center;justify-content:center;font-family:"Roboto",sans-serif;font-weight:500;font-size:14px;text-transform:uppercase;color:#fff;background:var(--red);box-shadow:0 4px 10px rgba(0,0,0,.25)}
.red-rule{width:130px;height:3px;background:var(--red)}
p.body-copy{font-size:13px;line-height:27.5px;color:var(--text)}

/* header */
.site-header{position:absolute;left:0;top:0;width:1200px;height:90px;background:#fff;display:flex;align-items:center}
.brand{position:absolute;left:111px;top:20px;display:flex;align-items:center;gap:8px}
.brand-square{width:14px;height:14px;background:var(--red)}
.brand-name{font-family:"Roboto",sans-serif;font-weight:700;font-size:17px;line-height:19px;color:var(--navy);text-transform:uppercase;width:120px}
.main-nav{position:absolute;left:479px;top:36px;display:flex;gap:28px;font-size:13px;font-weight:500;color:var(--ink);text-transform:uppercase}
.main-nav .active{color:var(--red)}
.phone-btn{position:absolute;left:933px;top:22px;width:154px;height:42px;font-size:13px;text-transform:none;gap:6px}

/* hero */
.hero{position:absolute;left:0;top:90px;width:1200px;height:652px;background:linear-gradient(180deg,#3b4350 0%,#1e2633 55%,#2a3344 100%)}
.hero-title{position:absolute;left:0;top:200px;width:1200px;text-align:center;font-family:"Oswald",sans-serif;font-weight:600;font-size:68px;color:#fff;letter-spacing:.5px}
.hero-copy{position:absolute;left:290px;top:290px;width:620px;text-align:center;font-size:13px;line-height:27px;color:#fff}
.hero-btn{position:absolute;left:505px;top:390px;width:190px;height:50px}
.hero-arrow{position:absolute;top:303px;width:48px;height:48px;border-radius:50%;background:var(--navy);display:flex;align-items:center;justify-content:center}
.hero-dots{position:absolute;left:563px;top:600px;display:flex;gap:5px}
.hero-dots span{width:10px;height:10px;border-radius:50%;border:1.5px solid #fff}
.hero-dots .on{background:#fff}

/* welcome */
.welcome{position:absolute;left:0;top:742px;width:1200px;height:737px;background:#fff}
.kicker{font-family:"Oswald",sans-serif;font-weight:500;font-size:16px;color:var(--red);text-transform:uppercase}
.about-photo{position:absolute;left:647px;top:126px;width:433px;height:492px;background:linear-gradient(180deg,#9aa4ae 0%,#c8ced4 45%,#274c8c 80%,#1b3d78 100%);border:6px solid #fff;box-shadow:0 6px 18px rgba(0,0,0,.25)}
.vertical-word{position:absolute;left:1065px;top:520px;transform:rotate(-90deg);transform-origin:left top;font-family:"Oswald",sans-serif;font-weight:600;font-size:78px;color:#ececec;letter-spacing:2px}

/* units */
.units{position:absolute;left:0;top:1479px;width:1200px;height:733px;background:linear-gradient(180deg,var(--navy) 0%,var(--navy-dark) 100%)}
.units .heading{color:#fff}
.unit-card{position:absolute;top:195px;width:309px;height:426px;background:#fff;padding:8px;box-shadow:0 8px 16px rgba(0,0,0,.3)}
.unit-photo{width:100%;height:235px;position:relative}
.unit-title{font-family:"Oswald",sans-serif;font-weight:500;font-size:15px;color:var(--navy);margin:22px 4px 8px;text-transform:uppercase}
.unit-text{font-size:12.5px;line-height:25px;margin:0 4px}
.unit-tags{display:flex;gap:10px;margin:14px 4px 0}
.unit-tags span{border:1px solid var(--line);font-size:12px;font-weight:500;color:var(--ink);padding:10px 14px;box-shadow:0 2px 4px rgba(0,0,0,.1)}
.unit-tags small{font-size:9px}

/* split */
.split{position:absolute;left:0;top:2212px;width:1200px;height:486px;background:#fff}
.split-photo{position:absolute;left:0;top:0;width:597px;height:486px;background:linear-gradient(135deg,#5f6d80 0%,#b9c1cb 50%,#7b8797 100%)}
.outline-btn{position:absolute;width:192px;height:54px;border:2px solid var(--red);color:var(--red);font-weight:500;font-size:14px;display:flex;align-items:center;justify-content:center}

/* sizes */
.sizes{position:absolute;left:0;top:2698px;width:1200px;height:954px;background:#fff}
.size-tile{position:absolute;width:317px;height:318px;background:#fff;border:1px solid #e4e4e4;padding:6px}
.size-photo{width:100%;height:258px}
.size-caption{text-align:center;font-family:"Oswald",sans-serif;font-weight:500;font-size:16px;color:var(--navy);margin-top:16px}
.size-tile.featured{background:var(--red);border-color:var(--red);box-shadow:0 6px 14px rgba(0,0,0,.3)}
.size-tile.featured .size-caption{color:#fff}
.size-offer{position:absolute;left:62px;top:54px;width:192px;height:160px;background:var(--navy);color:#fff;text-align:center;font-family:"Oswald",sans-serif;padding-top:26px}

/* contact */
.contact{position:absolute;left:0;top:3652px;width:1200px;height:690px;background:var(--mist)}
.field{position:absolute;height:40px;border-bottom:1.5px solid #555;font-size:14px;color:#666}
.submit-btn{position:absolute;left:505px;top:570px;width:190px;height:50px;background:var(--navy)}

/* footer */
.site-footer{position:absolute;left:0;top:4342px;width:1200px;height:424px;background:linear-gradient(180deg,var(--red) 0%,var(--red-dark) 100%);color:#fff}
.foot-brand{position:absolute;left:111px;top:74px;width:240px;text-align:center}
.foot-brand .brand-name{color:#fff;width:auto;font-size:34px;line-height:40px}
.cards{position:absolute;left:111px;top:270px;display:flex;gap:10px}
.cards span{width:47px;height:29px;background:#fff;border-radius:3px}
.foot-col{position:absolute;top:68px}
.foot-col h4{font-family:"Oswald",sans-serif;font-weight:500;font-size:18px}
.foot-col .bar{width:30px;height:2px;background:#fff;margin:10px 0 14px}
.foot-col li{list-style:none;font-size:13px;line-height:31px}
.foot-col .label{font-weight:500;font-size:13px;margin-top:8px}
.foot-col .val{font-size:13px;line-height:22px;display:flex;gap:6px;align-items:flex-start}
.foot-rule{position:absolute;left:111px;top:330px;width:978px;height:1px;background:rgba(255,255,255,.5)}
.socials{position:absolute;left:514px;top:357px;display:flex;gap:10px}
.socials span{width:48px;height:48px;border-radius:50%;border:1.5px solid #fff}
</style>
</head>
<body>

<header class="site-header">
  <div class="brand"><span class="brand-square"></span><span class="brand-name">Baycrest Self Storage</span></div>
  <nav class="main-nav">
    <span class="active">Home</span><span>About Us</span><span>Services</span><span>Units</span><span>Blog</span><span>Contact</span>
  </nav>
  <div class="btn phone-btn">
    <svg width="12" height="12" viewBox="0 0 24 24"><path fill="#fff" d="M6.6 10.8a15.1 15.1 0 0 0 6.6 6.6l2.2-2.2c.3-.3.7-.4 1-.2 1.1.4 2.3.6 3.6.6.6 0 1 .4 1 1V20c0 .6-.4 1-1 1A17 17 0 0 1 3 4c0-.6.4-1 1-1h3.5c.6 0 1 .4 1 1 0 1.3.2 2.5.6 3.6.1.3 0 .7-.2 1z"/></svg>
    +1 888 888 8888
  </div>
</header>

<section class="hero" role="img" aria-label="Dark warehouse interior with steel roof trusses and storage unit doors">
  <h1 class="hero-title">BAYCREST SELF STORAGE</h1>
  <p class="hero-copy">Lorem ipsum dolor sit amet, consectetur adipiscing elit, sed do eiusmod tempor incididunt ut labore et dolore magna aliqua. Ut enim ad minim veniam, quis nostrud exercitation ullamco laboris nisi ut aliquip ex ea commodo consequat. Duis aute irure dolor in reprehenderit</p>
  <div class="btn hero-btn">Unit</div>
  <div class="hero-arrow" style="left:42px"><svg width="14" height="14" viewBox="0 0 24 24"><path d="M15 5l-7 7 7 7" stroke="#fff" stroke-width="2.5" fill="none"/></svg></div>
  <div class="hero-arrow" style="left:1106px"><svg width="14" height="14" viewBox="0 0 24 24"><path d="M9 5l7 7-7 7" stroke="#fff" stroke-width="2.5" fill="none"/></svg></div>
  <div class="hero-dots"><span></span><span></span><span class="on"></span><span></span><span></span></div>
</section>

<section class="welcome">
  <div class="abs" style="left:111px;top:147px">
    <div class="kicker">Welcome To</div>
    <h2 class="heading" style="font-size:40px;color:var(--ink);margin-top:4px">Baycrest Self Storage</h2>
    <div class="red-rule" style="margin-top:8px"></div>
    <p class="body-copy" style="width:448px;margin-top:24px">Lorem ipsum dolor sit amet, consectetur adipiscing elit, sed do eiusmod tempor incididunt ut labore et dolore magna aliqua. Ut enim ad minim veniam, quis nostrud exercitation ullamco laboris nisi ut aliquip ex ea commodo consequat. Duis aute irure dolor in reprehenderit in voluptate velit esse cillum dolore eu fugiat nulla pariatur. Excepteur sint occaecat cupidatat non proident, sunt in culpa qui</p>
    <p class="body-copy" style="width:448px;margin-top:12px">Lorem ipsum dolor sit amet, consectetur adipiscing elit, sed do eiusmod tempor incididunt ut labore et dolore magna aliqua. Ut enim ad minim veniam, quis nostrud exercitation ullamco</p>
    <div class="btn" style="width:190px;height:48px;margin-top:24px">Read More</div>
  </div>
  <div class="about-photo" role="img" aria-label="Bright warehouse with tall pallet racks and a storage building with a padlock"></div>
  <div class="vertical-word">ABOUT US</div>
</section>

<section class="units">
  <h2 class="heading" style="position:absolute;left:0;top:88px;width:1200px;text-align:center;font-size:42px">Storage Units</h2>
  <article class="unit-card" style="left:111px">
    <div class="unit-photo" role="img" aria-label="Warehouse loading dock exterior" style="background:linear-gradient(180deg,#8fb0d0,#c9cfd6 60%,#9a9a9a)"></div>
    <h3 class="unit-title">Lorem ipsum dolor sit amet</h3>
    <p class="unit-text">Lorem ipsum dolor sit amet,adipiscing elit, sed do eiusmod tempor incididunt</p>
    <div class="unit-tags"><span>Size - 10 x 14</span><span>Price - $200/<small>Mo</small></span></div>
  </article>
  <article class="unit-card" style="left:446px">
    <div class="unit-photo" role="img" aria-label="Dim warehouse aisle with shelving" style="background:linear-gradient(180deg,#5c5f63,#8a8c8f 60%,#6d6f72)">
      <div class="btn" style="position:absolute;left:50px;top:92px;width:190px;height:48px;font-size:13px">Reserve Now</div>
    </div>
    <h3 class="unit-title">Lorem ipsum dolor sit amet</h3>
    <p class="unit-text">Lorem ipsum dolor sit amet,adipiscing elit, sed do eiusmod tempor incididunt</p>
    <div class="unit-tags"><span>Size - 10 x 14</span><span>Price - $200/<small>Mo</small></span></div>
  </article>
  <article class="unit-card" style="left:781px">
    <div class="unit-photo" role="img" aria-label="Blue pallet racks stocked with boxes" style="background:linear-gradient(180deg,#a9b8c8,#c4cbd2 50%,#7e93ad)"></div>
    <h3 class="unit-title">Lorem ipsum dolor sit amet</h3>
    <p class="unit-text">Lorem ipsum dolor sit amet,adipiscing elit, sed do eiusmod tempor incididunt</p>
    <div class="unit-tags"><span>Size - 10 x 14</span><span>Price - $200/<small>Mo</small></span></div>
  </article>
</section>

<section class="split">
  <div class="split-photo" role="img" aria-label="Forklift driver moving pallets between tall warehouse racks"></div>
  <div class="abs" style="left:642px;top:82px">
    <h2 class="heading" style="font-size:42px">Self Storage</h2>
    <div class="red-rule" style="margin-top:6px"></div>
    <p class="body-copy" style="width:448px;margin-top:22px">Lorem ipsum dolor sit amet, consectetur adipiscing elit, sed do eiusmod tempor incididunt ut labore et dolore magna aliqua. Ut enim ad minim veniam, quis nostrud exercitation ullamco laboris nisi ut aliquip ex ea commodo consequat. Duis aute irure dolor in reprehenderit in voluptate velit esse cillum dolore eu fugiat nulla pariatur. Excepteur sint occaecat cupidatat non proident, sunt in culpa qui</p>
  </div>
  <div class="outline-btn" style="left:642px;top:348px">READ MORE</div>
</section>

<section class="sizes">
  <h2 class="heading" style="position:absolute;left:0;top:94px;width:1200px;text-align:center;font-size:42px">Flexible Unit Sizes</h2>
  <div class="red-rule" style="position:absolute;left:535px;top:160px"></div>

  <div class="size-tile" style="left:111px;top:208px"><div class="size-photo" role="img" aria-label="Racks of boxed stock" style="background:linear-gradient(180deg,#6f8fb8,#c8a77a 55%,#d9dde2)"></div><div class="size-caption">Lorem ipsum dolor sit amet</div></div>
  <div class="size-tile" style="left:441px;top:208px"><div class="size-photo" role="img" aria-label="Long aisle of shelving" style="background:linear-gradient(180deg,#4f6c9a,#8a93a0 55%,#b7bcc3)"></div><div class="size-caption">Lorem ipsum dolor sit amet</div></div>
  <div class="size-tile" style="left:771px;top:208px"><div class="size-photo" role="img" aria-label="Empty warehouse hall" style="background:linear-gradient(180deg,#8b9097,#c3c6ca 55%,#e1e3e5)"></div><div class="size-caption">Lorem ipsum dolor sit amet</div></div>

  <div class="size-tile" style="left:111px;top:544px"><div class="size-photo" role="img" aria-label="Warehouse racks with cartons" style="background:linear-gradient(180deg,#9aa8b8,#bcb5a8 55%,#d4d7db)"></div><div class="size-caption">Lorem ipsum dolor sit amet</div></div>
  <div class="size-tile featured" style="left:441px;top:544px"><div class="size-photo" role="img" aria-label="Storage unit interior" style="background:linear-gradient(180deg,#3a3f47,#252a31)"></div>
    <div class="size-offer"><div style="font-size:24px">10 x 14 / <span style="font-size:12px">Ground Floor</span></div><div style="font-size:24px;margin-top:8px">$200 a month</div><div style="font-size:13px;text-decoration:underline;margin-top:10px">Reserve Now</div></div>
    <div class="size-caption">Lorem ipsum dolor sit amet</div></div>
  <div class="size-tile" style="left:771px;top:544px"><div class="size-photo" role="img" aria-label="Blue steel warehouse with pallet jack" style="background:linear-gradient(180deg,#3f68a8,#9fb2cc 55%,#cfd6de)"></div><div class="size-caption">Lorem ipsum dolor sit amet</div></div>
</section>

<section class="contact">
  <h2 class="heading" style="position:absolute;left:0;top:78px;width:1200px;text-align:center;font-size:42px">Contact Us</h2>
  <div class="red-rule" style="position:absolute;left:535px;top:146px"></div>
  <p class="body-copy" style="position:absolute;left:270px;top:156px;width:660px;text-align:center;line-height:26px">Lorem ipsum dolor sit amet, consectetur adipiscing elit, sed do eiusmod tempor incididunt ut labore et dolore magna aliqua. Ut enim ad</p>
  <div class="field" style="left:228px;top:236px;width:350px">Name</div>
  <div class="field" style="left:623px;top:236px;width:350px">Email</div>
  <div class="field" style="left:228px;top:306px;width:350px">Confirm Email</div>
  <div class="field" style="left:623px;top:306px;width:350px">Unit Number</div>
  <div class="field" style="left:228px;top:372px;width:742px;height:48px">Reason for contact
    <svg style="position:absolute;right:14px;top:4px" width="12" height="12" viewBox="0 0 24 24"><path d="M5 9l7 7 7-7" stroke="#666" stroke-width="2" fill="none"/></svg></div>
  <div class="field" style="left:228px;top:446px;width:742px;height:78px">Message</div>
  <div class="btn submit-btn">Submit</div>
</section>

<footer class="site-footer">
  <div class="foot-brand"><div class="brand-name">BAYCREST<br><span style="font-size:20px;letter-spacing:2px">SELF STORAGE</span></div></div>
  <div class="cards" aria-label="Accepted payment cards"><span></span><span></span><span></span><span></span><span></span></div>

  <div class="foot-col" style="left:528px"><h4>QUICK LINKS</h4><div class="bar"></div>
    <ul><li>Home</li><li>About Us</li><li>Services</li><li>Units</li><li>Blog</li><li>Contact</li></ul></div>
  <div class="foot-col" style="left:698px"><h4>SUPPORT</h4><div class="bar"></div>
    <ul><li>Help</li><li>Information</li><li>Legal Policy</li></ul></div>
  <div class="foot-col" style="left:865px;width:224px"><h4>CONTACT US</h4><div class="bar"></div>
    <div class="label">ADDRESS</div>
    <div class="val"><svg width="10" height="14" viewBox="0 0 24 32"><path fill="#fff" d="M12 0a12 12 0 0 0-12 12c0 9 12 20 12 20s12-11 12-20A12 12 0 0 0 12 0zm0 17a5 5 0 1 1 0-10 5 5 0 0 1 0 10z"/></svg>Lorem ipsum dolor sit amet</div>
    <div class="label" style="margin-top:14px">PHONE</div>
    <div class="val"><svg width="12" height="12" viewBox="0 0 24 24"><path fill="#fff" d="M6.6 10.8a15.1 15.1 0 0 0 6.6 6.6l2.2-2.2c.3-.3.7-.4 1-.2 1.1.4 2.3.6 3.6.6.6 0 1 .4 1 1V20c0 .6-.4 1-1 1A17 17 0 0 1 3 4c0-.6.4-1 1-1h3.5c.6 0 1 .4 1 1 0 1.3.2 2.5.6 3.6.1.3 0 .7-.2 1z"/></svg>+1 888-888-8888</div>
    <div class="label" style="margin-top:14px">Hours</div>
    <div class="val"><svg width="12" height="12" viewBox="0 0 24 24"><circle cx="12" cy="12" r="10" stroke="#fff" stroke-width="2.5" fill="none"/><path d="M12 6v6l4 2" stroke="#fff" stroke-width="2.5" fill="none"/></svg>9:30 AM - 5:30 PM,<br>7 days a week</div>
  </div>

  <div class="foot-rule"></div>
  <div class="abs" style="left:111px;top:374px;font-size:13px">© 2022 All Rights Reserved</div>
  <div class="socials" aria-label="Social links"><span></span><span></span><span></span></div>
  <div class="abs" style="left:915px;top:374px;font-size:13px">Terms of use | Privacy Policy</div>
</footer>

</body>
</html>
```